Corvane Holdings , new business card design

investment firm with corporate clients . need double sided business card , vertical and horizontal options ,logo must be clear. prefer pantone colors only and sharp design. website also www.corvane.ae

Khalid Bin Tarrafi
Managing Director
Tel. +971 4 387 2940
Mobile +971 50 518 2403
khalid@corvane.ae
Q-Span Plaza, officw 18-B07, Warqa Gardens, Dubai

Contact Information for Business Card

Khalid Bin Tarrafi
Managing Director

Font styles to use
Serif

Colors

Designer to choose colors to be used in the design.

```html
<!DOCTYPE html>
<html lang="en">
<head>
<meta charset="utf-8">
<title>Corvane Holdings — Business Card</title>
<link href="https://fonts.googleapis.com/css2?family=Jost:wght@400;600&display=swap" rel="stylesheet">
<style>
  :root {
    --backdrop: #8c8c8c;
    --card-light: #f4f4f4;
    --brand-blue: #46739c;
    --ink: #1e1e1e;
    --white: #ffffff;
  }
  * { margin: 0; padding: 0; box-sizing: border-box; }
  html, body { width: 1200px; height: 1200px; overflow: hidden; }
  body {
    background: var(--backdrop);
    font-family: "Jost", "Century Gothic", sans-serif;
    position: relative;
  }
  .card {
    position: absolute;
    top: 310px;
    height: 594px;
    box-shadow: 2px 3px 6px rgba(0,0,0,0.35);
  }
  .card--front { left: 234px; width: 364px; background: var(--card-light); color: var(--ink); }
  .card--back { left: 628px; width: 368px; background: var(--brand-blue); color: var(--white); }

  .wordmark {
    position: absolute;
    left: 0; right: 0;
    text-align: center;
    font-weight: 400;
    font-size: 25px;
    letter-spacing: 5px;
    text-indent: 5px;
    white-space: nowrap;
  }
  .card--front .wordmark { top: 170px; color: var(--ink); }
  .card--back .wordmark { top: 300px; color: var(--white); }

  .contact-block {
    position: absolute;
    top: 318px;
    left: 0; right: 0;
    text-align: center;
    font-size: 17px;
    line-height: 21.5px;
  }
  .person-name {
    color: var(--brand-blue);
    font-weight: 600;
    font-size: 19px;
    letter-spacing: 0.2px;
  }
  .person-role { font-size: 17px; }
  .rule {
    width: 198px;
    height: 1px;
    background: var(--ink);
    margin: 10px auto 11px;
  }
  .contact-label { color: var(--brand-blue); font-weight: 600; }
  .address { line-height: 21px; }

  .back-url {
    position: absolute;
    top: 516px;
    left: 0; right: 0;
    text-align: center;
    font-size: 17px;
    letter-spacing: 1.6px;
  }
</style>
</head>
<body>
  <section class="card card--front" aria-label="Business card front">
    <div class="wordmark">CORVANE HOLDINGS</div>
    <div class="contact-block">
      <div class="person-name">KHALID BIN TARRAFI</div>
      <div class="person-role">Managing Director</div>
      <div class="rule"></div>
      <div><span class="contact-label">P:</span> +971 4 387 2940</div>
      <div><span class="contact-label">M:</span> +971 50 518 2403</div>
      <div><span class="contact-label">E:</span> khalid@corvane.ae</div>
      <div><span class="contact-label">W:</span> www.corvane.ae</div>
      <div class="rule"></div>
      <div class="address">Q-Span Plaza, officw 18-B07<br>Warqa Gardens, Dubai</div>
    </div>
  </section>

  <section class="card card--back" aria-label="Business card back">
    <div class="wordmark">CORVANE HOLDINGS</div>
    <div class="back-url">www.corvane.ae</div>
  </section>
</body>
</html>
```